The most modern business card ever !!!

Our company call “Vendalo”. Vendalo is a technology company specialized in cruises solutions. Out main product is a platform to reserve cruises. This is a revolutionary platform that make easier to travel agencies and final users to reserve cruises across dozen companies like tibba, wernu, hpv, dgb, etc..We are a “start up”, with a young team of developers and we want to transmit it.. For it, we want something different, a modern business card that represent cruises and technology.. When someone receive this card, this person should say: wowww this is different… this is modern… this is a cruise related company..
- diferent, modern
- traditions business card

```html
<!DOCTYPE html>
<html lang="en">
<head>
<meta charset="utf-8">
<title>Vendalo — Business Card</title>
<link href="https://fonts.googleapis.com/css2?family=Roboto:wght@400;500&display=swap" rel="stylesheet">
<style>
  :root {
    --page-bg: #ecebe8;
    --card-white: #ffffff;
    --charcoal: #3a3d3f;
    --charcoal-deep: #323537;
    --ice-blue: #d3e3ea;
    --accent-blue: #2ea3dd;
    --ink: #111111;
    --ink-soft: #2b2b2b;
  }
  * { margin: 0; padding: 0; box-sizing: border-box; }
  html, body {
    width: 1200px; height: 1200px; overflow: hidden;
    background: var(--page-bg);
    font-family: "Roboto", Arial, sans-serif;
  }
  .stage { position: relative; width: 1200px; height: 1200px; }

  .card {
    position: absolute; top: 254px;
    width: 416px; height: 694px;
    background: var(--card-white);
    box-shadow: 0 6px 18px rgba(0,0,0,0.18);
    overflow: hidden;
  }
  .card--front { left: 156px; }
  .card--back  { left: 629px; }

  /* Front */
  .front-top {
    position: absolute; left: 0; top: 0; width: 100%; height: 415px;
    background: radial-gradient(circle at 50% 45%, #44484a 0%, var(--charcoal) 45%, var(--charcoal-deep) 100%);
  }
  .front-wordmark {
    position: absolute; left: 0; right: 0; top: 160px;
    text-align: center;
    font-weight: 500; font-size: 66px; letter-spacing: 3px;
    color: var(--card-white);
  }
  .bar-pair { position: absolute; display: flex; }
  .bar-pair--vertical { left: 72px; top: 518px; gap: 10px; }
  .bar-pair--vertical .bar { width: 8px; height: 52px; }
  .bar--ink { background: var(--ink); }
  .bar--blue { background: var(--accent-blue); }

  .front-identity { position: absolute; left: 136px; top: 522px; }
  .person-name {
    font-weight: 500; font-size: 19px; letter-spacing: 2.4px; color: var(--ink);
    white-space: nowrap;
  }
  .person-role {
    font-weight: 400; font-size: 16px; letter-spacing: 1.8px; color: var(--ink-soft);
    margin-top: 3px; white-space: nowrap;
  }

  /* Back */
  .back-lower {
    position: absolute; left: 0; top: 252px; width: 100%; height: 442px;
    background: var(--ice-blue);
  }
  .logo-tab {
    position: absolute; left: 302px; top: 80px; width: 114px; height: 323px;
    background: var(--charcoal);
    border-radius: 30px 0 0 30px;
    display: flex; align-items: center; justify-content: center;
  }
  .logo-tab__wordmark {
    writing-mode: vertical-rl; transform: rotate(180deg);
    font-weight: 500; font-size: 64px; letter-spacing: 2px;
    color: var(--card-white); white-space: nowrap;
  }
  .back-identity {
    position: absolute; left: 72px; top: 100px; height: 216px;
    writing-mode: vertical-rl; transform: rotate(180deg);
  }
  .back-identity .person-name { letter-spacing: 3px; }
  .back-identity .person-role { margin-top: 0; margin-left: 4px; }

  .bar-pair--horizontal { left: 63px; top: 352px; flex-direction: column; gap: 6px; }
  .bar-pair--horizontal .bar { width: 52px; height: 7px; }

  .divider-rule {
    position: absolute; left: 63px; top: 498px; width: 116px; height: 7px;
    background: var(--ink);
  }
  .contact-list {
    position: absolute; left: 63px; top: 538px; list-style: none;
    font-size: 18px; letter-spacing: 1.4px; color: var(--ink);
    white-space: nowrap;
  }
  .contact-list li { height: 36px; line-height: 22px; }
</style>
</head>
<body>
<main class="stage">
  <section class="card card--front">
    <div class="front-top">
      <div class="front-wordmark">Vendalo</div>
    </div>
    <div class="bar-pair bar-pair--vertical">
      <span class="bar bar--ink"></span>
      <span class="bar bar--blue"></span>
    </div>
    <div class="front-identity">
      <p class="person-name">Your Name Here</p>
      <p class="person-role">Designation</p>
    </div>
  </section>

  <section class="card card--back">
    <div class="back-lower"></div>
    <div class="logo-tab">
      <span class="logo-tab__wordmark">Vendalo</span>
    </div>
    <div class="back-identity">
      <p class="person-name">Your Name Here</p>
      <p class="person-role">Designation</p>
    </div>
    <div class="bar-pair bar-pair--horizontal">
      <span class="bar bar--blue"></span>
      <span class="bar bar--ink"></span>
    </div>
    <div class="divider-rule"></div>
    <ul class="contact-list">
      <li>- Hello@vendalo.io</li>
      <li>- 555 +0147 2836 904</li>
      <li>- Harbor Quay Road 48. Portside</li>
    </ul>
  </section>
</main>
</body>
</html>
```